Preschool Website

Looking to have a one page splash with a contact us form that uses some kind of verification to keep bots from filling out the form. We would like for it to be dynamic for both mobile and desktop. Would like to have it show up in search engines for preschool in are area. Would like to include a link to the website are current parents use for payment information.

Target Market(s)

Young Adults with Childrens

Industry/Entity Type

Preschool

Coding

Coded - Design and coding required

Number of Pages Required

1 page

Colors

Designer to choose colors to be used in the design.

Requirements
Must have
• Searchable in Quorla
• Contact us form
• Name
• Phone
• Email
• Message box
• Form must have code entered to submit to prevent junk emails
• Link to the website we use for parents to make payments
• our phone and address clickable on device to make call or map on phone
Should not have
• more then one page

```html
<!DOCTYPE html>
<html lang="en">
<head>
<meta charset="utf-8">
<title>Linden Preschool – Contact Us</title>
<link rel="stylesheet" href="https://fonts.googleapis.com/css2?family=Cabin+Condensed:wght@700&family=Cabin+Sketch:wght@700&family=Poppins:wght@400;600&display=swap">
<style>
  :root{
    --teal:#0b7a66;
    --teal-dark:#04584a;
    --teal-light:#16927b;
    --orange:#fb9a06;
    --ink:#222222;
    --white:#ffffff;
    --paper:#f4f7f8;
    --field-border:#8c8c8c;
  }
  *{box-sizing:border-box;margin:0;padding:0}
  html,body{width:1200px;height:1029px;overflow:hidden;background:var(--white)}
  body{position:relative;font-family:'Poppins',sans-serif;color:var(--ink)}

  .site-header{position:absolute;left:0;top:0;width:1200px;height:90px}
  .brand{position:absolute;left:111px;top:21px;height:48px;display:flex;align-items:center;gap:10px;
    font-family:'Cabin Condensed',sans-serif;font-weight:700;font-size:40px;line-height:1;color:var(--ink);letter-spacing:.3px}
  .brand-dot{width:40px;height:40px;border-radius:50%;background:var(--orange)}
  .nav-btn{position:absolute;top:18px;height:53px;display:flex;align-items:center;justify-content:center;
    font-family:'Cabin Condensed',sans-serif;font-weight:700;font-size:22px;color:var(--white);text-decoration:none;border-radius:2px}
  .nav-contact{left:827px;width:140px;background:var(--orange)}
  .nav-payment{left:981px;width:107px;background:var(--teal)}

  .hero-band{position:absolute;left:0;top:86px;width:1200px;height:855px}
  .hero-title{position:absolute;left:0;top:0;width:1200px;height:0;text-align:center;color:var(--white);
    font-family:'Cabin Sketch',sans-serif;font-weight:700;line-height:1}
  .hero-title .small{position:absolute;left:0;right:0;top:173px;font-size:42px}
  .hero-title .large{position:absolute;left:0;right:0;top:216px;font-size:62px}

  .kids{position:absolute;border-radius:60px}
  .kids-left{left:187px;top:343px;width:242px;height:488px;
    background:linear-gradient(180deg,#c65a2a 0%,#f0b496 45%,#d8622e 70%,#f0b496 100%)}
  .kids-right{left:801px;top:309px;width:210px;height:527px;
    background:linear-gradient(180deg,#a33a16 0%,#f0b496 40%,#8a5a36 65%,#eeeeee 100%)}

  .paper{position:absolute;left:365px;top:313px;width:479px;height:525px;background:var(--paper)}

  .paper-heading{position:absolute;left:365px;top:358px;width:479px;text-align:center;line-height:1;
    font-family:'Cabin Condensed',sans-serif;font-weight:700;font-size:36px;color:var(--teal)}

  .contact-form{position:absolute;left:447px;top:419px;width:305px;height:393px;background:var(--white);
    box-shadow:0 1px 4px rgba(0,0,0,.12)}
  .field{position:absolute;left:40px;width:230px;height:38px;border:2px solid var(--field-border);border-radius:3px;
    font-family:'Poppins',sans-serif;font-size:15px;color:var(--ink);padding:0 7px;background:var(--white)}
  .field::placeholder{color:#333}
  textarea.field{height:65px;padding-top:5px;resize:none}
  .f-name{top:21px}.f-phone{top:74px}.f-email{top:126px}.f-message{top:178px}.f-code{top:291px}
  .captcha{position:absolute;left:42px;top:257px;width:117px;height:22px;
    background:linear-gradient(90deg,#111 0%,#555 60%,#ccc 100%)}
  .submit{position:absolute;left:40px;top:340px;width:93px;height:39px;background:var(--orange);border:0;border-radius:2px;
    color:var(--white);font-family:'Poppins',sans-serif;font-weight:600;font-size:16px}

  .site-footer{position:absolute;left:0;top:979px;width:1200px;text-align:center;font-size:17px;line-height:24px;color:var(--ink)}
</style>
</head>
<body>
  <header class="site-header">
    <div class="brand"><span class="brand-dot"></span>LINDEN PRESCHOOL</div>
    <a class="nav-btn nav-contact" href="#contact">CONTACT US</a>
    <a class="nav-btn nav-payment" href="#payment">PAYMENT</a>
  </header>

  <svg class="hero-band" viewBox="0 0 1200 855" aria-hidden="true">
    <defs>
      <radialGradient id="bandGlow" cx="50%" cy="50%" r="60%">
        <stop offset="0" stop-color="#16927b"/>
        <stop offset="1" stop-color="#04584a"/>
      </radialGradient>
    </defs>
    <path d="M0 14 C120 40 220 36 330 18 C420 2 520 4 620 20 C760 42 900 10 1000 10 C1080 10 1140 24 1200 18
             L1200 840 C1100 820 1000 800 880 810 C760 822 640 850 520 832 C400 812 260 800 140 816 C80 824 30 838 0 842 Z"
          fill="url(#bandGlow)"/>
  </svg>

  <h1 class="hero-title"><span class="small">WELCOME TO</span><span class="large">LINDEN PRESCHOOL</span></h1>

  <div class="kids kids-left" role="img" aria-label="Illustration of two smiling cartoon children holding pencils and scissors"></div>
  <div class="kids kids-right" role="img" aria-label="Illustration of two smiling cartoon children, one with glasses and a magnifying glass"></div>

  <div class="paper" role="img" aria-label="Illustration of a torn sheet of ruled notebook paper"></div>

  <h2 class="paper-heading" id="contact">CONTACT US</h2>

  <form class="contact-form">
    <input class="field f-name" type="text" placeholder="Name:">
    <input class="field f-phone" type="tel" placeholder="Phone:">
    <input class="field f-email" type="email" placeholder="Email:">
    <textarea class="field f-message" placeholder="Message:"></textarea>
    <div class="captcha" role="img" aria-label="Verification code image"></div>
    <input class="field f-code" type="text" placeholder="Enter above text">
    <button class="submit" type="submit">Submit</button>
  </form>

  <footer class="site-footer">Copyrights @ 2019 Linden Preschool. All Rights Reserved.</footer>
</body>
</html>
```